Irrigation Business needs their business cards modernised and revamped

I would like to keep my current logo, colours and revamp the format of the card.

I would like the card to be clean yet important.

Im not sure if you include texture but i would like the named logo to be indented into the card etc.

show me something alive and free something thats clinical to the point yet has a feel of achievement. i would like people to go nice card.

Target Market(s)

high end clients, corporate, sports field manger, the guys that make the decisions

Industry/Entity Type

Business

Contact Information for Business Card

nformation to be included

Dean Harlow (Director)
0487305526
dean@kolvat.biz
www.kestonfieldworks.com

instagram logo
google logo
facebook logo

Colors

Designer to choose colors to be used in the design.

Requirements
Nice to have
• indentations a really nice feel to the card good texture

```html
<!DOCTYPE html>
<html lang="en">
<head>
<meta charset="utf-8">
<title>Keston Fieldworks — Business Cards</title>
<link rel="stylesheet" href="https://fonts.googleapis.com/css2?family=Open+Sans:wght@400;600;700;800&display=swap">
<style>
  :root {
    --bg: #e9ebee;
    --blue-deep: #2a63b0;
    --blue-bright: #2ea6dc;
    --brand-blue: #2467b3;
    --sky: #1e9bd7;
    --ink: #4a4f55;
    --muted: #6b7077;
    --rule: #9fcde6;
    --paper: #ffffff;
    --emboss: #f4f7fa;
  }
  * { box-sizing: border-box; margin: 0; padding: 0; }
  html, body { width: 1200px; height: 900px; overflow: hidden; }
  body {
    background: var(--bg);
    font-family: "Open Sans", Arial, sans-serif;
    position: relative;
  }
  .card {
    position: absolute;
    width: 560px;
    height: 320px;
    border-radius: 4px;
    box-shadow: 0 10px 28px rgba(30, 40, 60, 0.18);
    overflow: hidden;
  }
  /* Front */
  .card--front {
    left: 90px;
    top: 100px;
    background: radial-gradient(ellipse at 62% 40%, var(--blue-bright) 0%, #2b8ccf 45%, var(--blue-deep) 100%);
  }
  .front-mark {
    position: absolute;
    left: 50%;
    top: 120px;
    transform: translate(-50%, -50%);
    display: flex;
    flex-direction: column;
    align-items: center;
    gap: 12px;
  }
  .front-mark__disc {
    width: 92px;
    height: 92px;
    border-radius: 50%;
    background: var(--emboss);
    box-shadow: inset 0 -3px 6px rgba(0,0,0,0.18), 0 3px 8px rgba(0,0,0,0.25);
  }
  .front-mark__name {
    font-weight: 700;
    font-size: 18px;
    letter-spacing: 1px;
    color: var(--emboss);
    text-transform: uppercase;
  }
  .social-row {
    position: absolute;
    left: 50%;
    top: 262px;
    transform: translateX(-50%);
    display: flex;
    gap: 10px;
  }
  .social-row__dot {
    width: 22px;
    height: 22px;
    border-radius: 50%;
    background: var(--emboss);
    box-shadow: 0 1px 3px rgba(0,0,0,0.25);
  }
  /* Back */
  .card--back {
    left: 550px;
    top: 480px;
    background: var(--paper);
  }
  .brand-block {
    position: absolute;
    left: 36px;
    top: 92px;
    width: 250px;
    display: flex;
    flex-direction: column;
    align-items: center;
    gap: 10px;
  }
  .brand-block__disc {
    width: 70px;
    height: 70px;
    border-radius: 50%;
    background: var(--sky);
  }
  .brand-block__name {
    font-weight: 800;
    font-size: 23px;
    line-height: 1.05;
    color: var(--brand-blue);
    text-transform: uppercase;
    text-align: center;
  }
  .divider {
    position: absolute;
    left: 304px;
    top: 58px;
    width: 1px;
    height: 150px;
    background: var(--rule);
  }
  .contact {
    position: absolute;
    left: 322px;
    top: 60px;
  }
  .contact__name {
    font-weight: 600;
    font-size: 18px;
    text-transform: uppercase;
    color: var(--brand-blue);
    line-height: 1.1;
  }
  .contact__name .surname { color: var(--sky); }
  .contact__role {
    font-size: 12.5px;
    color: var(--muted);
    margin-top: 2px;
  }
  .contact__list {
    list-style: none;
    margin-top: 26px;
    display: flex;
    flex-direction: column;
    gap: 5px;
  }
  .contact__item {
    display: flex;
    align-items: center;
    gap: 6px;
    font-size: 12.5px;
    color: var(--ink);
  }
  .contact__icon { width: 14px; height: 14px; flex: none; }
</style>
</head>
<body>
  <section class="card card--front" aria-label="Card front">
    <div class="front-mark">
      <div class="front-mark__disc"></div>
      <div class="front-mark__name">Keston Fieldworks</div>
    </div>
    <div class="social-row" aria-label="Social media">
      <span class="social-row__dot"></span>
      <span class="social-row__dot"></span>
      <span class="social-row__dot"></span>
    </div>
  </section>

  <section class="card card--back" aria-label="Card back">
    <div class="brand-block">
      <div class="brand-block__disc"></div>
      <div class="brand-block__name">Keston Fieldworks</div>
    </div>
    <div class="divider"></div>
    <div class="contact">
      <div class="contact__name">Dean <span class="surname">Harlow</span></div>
      <div class="contact__role">Director</div>
      <ul class="contact__list">
        <li class="contact__item">
          <svg class="contact__icon" viewBox="0 0 14 14" aria-hidden="true">
            <circle cx="7" cy="7" r="7" fill="var(--brand-blue)"/>
            <path d="M4.3 3.8c.4-.4.9-.4 1.1 0l.6 1.1c.2.3.1.6-.2.8l-.4.3c.4.9 1.1 1.6 2 2l.3-.4c.2-.3.5-.4.8-.2l1.1.6c.4.2.4.7 0 1.1-.6.6-1.4.8-2.2.4-1.6-.8-2.7-1.9-3.5-3.5-.4-.8-.2-1.6.4-2.2z" fill="#fff"/>
          </svg>
          0487305526
        </li>
        <li class="contact__item">
          <svg class="contact__icon" viewBox="0 0 14 14" aria-hidden="true">
            <circle cx="7" cy="7" r="7" fill="var(--brand-blue)"/>
            <rect x="3.5" y="4.5" width="7" height="5" rx="0.6" fill="#fff"/>
            <path d="M3.7 4.8 7 7.3l3.3-2.5" fill="none" stroke="var(--brand-blue)" stroke-width="0.8"/>
          </svg>
          dean@kolvat.biz
        </li>
        <li class="contact__item">
          <svg class="contact__icon" viewBox="0 0 14 14" aria-hidden="true">
            <circle cx="7" cy="7" r="7" fill="var(--brand-blue)"/>
            <path d="M7 3.2a2.5 2.5 0 0 0-2.5 2.5C4.5 7.6 7 10.8 7 10.8s2.5-3.2 2.5-5.1A2.5 2.5 0 0 0 7 3.2z" fill="#fff"/>
            <circle cx="7" cy="5.7" r="0.9" fill="var(--brand-blue)"/>
          </svg>
          www.kestonfieldworks.com
        </li>
      </ul>
    </div>
  </section>
</body>
</html>
```